Business Card Design needed for start up company Halvora

In need of a new business card designed for a start up company based in Sydney, Halvora is a new start up innovative Company, our mission it to make property accessible for everyday Australian and to become the leading Real Estate platform in Australia. We want it to be fresh and clean.

Industry/Entity Type

Financial

Contact Information for Business Card

Section for Name
Section for Title

HALVORA - The Strength of Pooling
Mobile:
Direct:

Font styles to use
Sans Serif

Colors
33a6d7
0692cd
0255a3
ffffff

Requirements
Must have
• Logo, all business card details

```html
<!DOCTYPE html>
<html lang="en">
<head>
<meta charset="utf-8">
<title>Halvora Business Card</title>
<link rel="stylesheet" href="https://fonts.googleapis.com/css2?family=Open+Sans:wght@400;600;700;800&display=swap">
<style>
  :root {
    --sky: #33a6d7;
    --cyan-light: #35d0e6;
    --ocean: #0692cd;
    --navy: #0255a3;
    --ink: #1f4f8f;
    --white: #ffffff;
    --paper: #f7f7f6;
    --grey-text: #5a5f66;
    --rule: #9aa0a6;
    --stage: #e6e8eb;
  }
  * { margin: 0; padding: 0; box-sizing: border-box; }
  html, body {
    width: 1200px; height: 900px; overflow: hidden;
    background: var(--stage);
    font-family: "Open Sans", Arial, sans-serif;
  }
  .canvas { position: relative; width: 1200px; height: 900px; }
  .card {
    position: absolute; left: 260px; width: 680px; height: 388px;
    box-shadow: 0 6px 18px rgba(0,0,0,0.18);
    overflow: hidden;
  }
  /* Front */
  .card-front {
    top: 48px;
    background: linear-gradient(100deg, var(--cyan-light) 0%, var(--sky) 45%, var(--ocean) 100%);
  }
  .front-brand {
    position: absolute; left: 0; right: 0; top: 130px;
    display: flex; justify-content: center; align-items: center; gap: 14px;
  }
  .brand-dot { width: 76px; height: 76px; border-radius: 50%; flex: none; }
  .front-brand .brand-dot { background: var(--white); }
  .brand-name {
    font-weight: 800; font-size: 66px; line-height: 1; letter-spacing: 1px;
  }
  .front-brand .brand-name { color: var(--white); }
  .tagline {
    position: absolute; left: 0; right: 0; top: 246px;
    text-align: center; color: var(--white); font-size: 16px; font-weight: 400;
  }
  /* Back */
  .card-back { top: 464px; background: var(--paper); }
  .back-brand {
    position: absolute; left: 60px; top: 64px;
    display: flex; align-items: center; gap: 12px;
  }
  .back-brand .brand-dot { background: var(--sky); width: 76px; height: 76px; }
  .back-brand .brand-name { color: var(--ink); font-size: 56px; }
  .rule { position: absolute; height: 1px; background: var(--rule); }
  .rule-top { left: 440px; right: 40px; top: 150px; }
  .address {
    position: absolute; right: 44px; top: 162px;
    text-align: right; color: var(--grey-text);
    font-size: 15px; line-height: 21px; font-style: normal;
  }
  .person {
    position: absolute; left: 40px; right: 40px; top: 250px;
    display: flex; align-items: center; gap: 12px;
  }
  .person .rule { position: static; flex: 1; }
  .person-name { font-size: 18px; font-weight: 700; color: var(--ink); white-space: nowrap; }
  .person-title { color: var(--sky); font-weight: 400; }
  .contacts {
    position: absolute; left: 44px; top: 290px;
    list-style: none; color: var(--grey-text); font-size: 15px; line-height: 22px;
  }
  .contacts li { display: flex; align-items: center; gap: 9px; }
  .contacts svg { width: 14px; height: 14px; fill: var(--ink); flex: none; }
</style>
</head>
<body>
<main class="canvas">
  <section class="card card-front" aria-label="Card front">
    <div class="front-brand">
      <span class="brand-dot" aria-hidden="true"></span>
      <span class="brand-name">HALVORA</span>
    </div>
    <p class="tagline">The Strength of Pooling</p>
  </section>

  <section class="card card-back" aria-label="Card back">
    <div class="back-brand">
      <span class="brand-dot" aria-hidden="true"></span>
      <span class="brand-name">HALVORA</span>
    </div>
    <div class="rule rule-top"></div>
    <address class="address">
      42 Wattle Street<br>
      Surry Hills, NSW 2010<br>
      www.halvora.co
    </address>

    <div class="person">
      <span class="rule"></span>
      <span class="person-name">MARA ELLISON - <span class="person-title">CEO/FOUNDER</span></span>
      <span class="rule"></span>
    </div>

    <ul class="contacts">
      <li>
        <svg viewBox="0 0 16 16" aria-hidden="true"><path d="M2 5c0-2 2-3 6-3s6 1 6 3v1h-3V4.5H5V6H2zM4 7h8l2 6v1H2v-1zm4 1.5a2 2 0 100 4 2 2 0 000-4z"/></svg>
        <span>Direct: 612 480 3175</span>
      </li>
      <li>
        <svg viewBox="0 0 16 16" aria-hidden="true"><path d="M5 1h6a1 1 0 011 1v12a1 1 0 01-1 1H5a1 1 0 01-1-1V2a1 1 0 011-1zm.5 2v9h5V3zM8 12.6a.7.7 0 100 1.4.7.7 0 000-1.4z"/></svg>
        <span>Mobile: 704 215 6938</span>
      </li>
      <li>
        <svg viewBox="0 0 16 16" aria-hidden="true"><path d="M1 4h14v9H1zm1.2 1L8 9l5.8-4z"/></svg>
        <span>mara@halvora.co</span>
      </li>
    </ul>
  </section>
</main>
</body>
</html>
```